Indoor Air Restoration company needs graphic design for a 6x12 v nose trailer to wrap

We offer mold services, duct cleaning, water damage clean up and odor removal. "We find, fix and prevent mold, odor and allergen problems" is what we want to communicate on this trailer, which is a rolling billboard. We like the blue and orange color themes, as found in our logo. The company name is Brightwater Dwelling Services and the logo is attached below. We'd like to see our message clearly, company name and what we offer. We tend to lean towards white letters on a darker background (blue or orange) but are very open to outside ideas, as we are stuck! Our website is available for reference if that is helpful. www.brightwaterdwell.com The phone number to be printed on truck is 302-517-9046, Happy designing!!

Target Market(s)

Home owners

Industry/Entity Type

Indoor Air Quality, Mold Remediation

Font styles to use
Sans Serif

Colors
0054AA
0677BA
7BADD7
CADEEF
E8F1F8
F0912C
F2A743
F7CA91
FBE8D2
FDF5EE

Requirements
Must have
• our message, company name and phone
Nice to have
• services we offer (mold remediation, duct cleaning, water damage and odor removal
Should not have
• cartoon feel

```html
<!DOCTYPE html>
<html lang="en">
<head>
<meta charset="utf-8">
<title>Brightwater Dwelling Services – Trailer Wrap Options</title>
<link rel="stylesheet" href="https://fonts.googleapis.com/css2?family=Barlow+Condensed:wght@500;600;700&family=Barlow:wght@700;800&display=swap">
<style>
  :root {
    --navy: #0054AA;
    --blue: #0677BA;
    --sky: #7BADD7;
    --mist: #CADEEF;
    --ice: #E8F1F8;
    --orange: #F0912C;
    --amber: #F2A743;
    --white: #ffffff;
    --indigo: #27245c;
    --lime: #8cc63f;
    --label: #1a9ee0;
  }
  * { margin: 0; padding: 0; box-sizing: border-box; }
  html, body { width: 848px; height: 1200px; overflow: hidden; background: #ffffff; }
  body { position: relative; font-family: "Barlow Condensed", "Arial Narrow", sans-serif; }

  .option { position: absolute; left: 51px; width: 746px; height: 354px; overflow: hidden; }
  .option > * { position: absolute; white-space: nowrap; line-height: 1; }
  .option-label {
    position: absolute; left: 735px; width: 87px; height: 17px;
    background: var(--label); color: var(--white);
    font-size: 12px; font-weight: 500; letter-spacing: 0.5px;
    display: flex; align-items: center; justify-content: center;
  }

  .brand-name { color: var(--blue); font-weight: 700; letter-spacing: 0.5px; text-align: center; }
  .brand-name .line { display: block; }
  .dot { color: var(--orange); }
  .sep { color: var(--orange); font-weight: 500; padding: 0 4px; }

  /* Option 1 */
  .option-dark { top: 51px; background: linear-gradient(90deg, #05070f 0%, #0b1a3a 45%, #0d3f8a 75%, #1b7fd6 100%); }
  .option-dark .backdrop { left: 360px; top: 0; width: 386px; height: 354px;
    background: linear-gradient(120deg, rgba(6,119,186,0) 0%, rgba(6,119,186,0.55) 45%, rgba(80,170,240,0.8) 75%, rgba(14,70,170,0.9) 100%); }
  .option-dark .brand-name { left: 89px; top: 120px; width: 267px; }
  .option-dark .brand-name .big { font-size: 48px; }
  .option-dark .brand-name .small { font-size: 31px; margin-top: 4px; }
  .option-dark .phone { left: 89px; top: 226px; font-size: 62px; font-weight: 600; color: var(--white); letter-spacing: -1px; }
  .option-dark .headline-a { left: 372px; top: 80px; font-size: 66px; font-weight: 600; color: var(--orange); }
  .option-dark .headline-a .light { color: var(--white); }
  .option-dark .headline-b { left: 372px; top: 146px; font-size: 63px; font-weight: 600; color: var(--orange); }
  .option-dark .services { left: 374px; top: 218px; font-size: 27px; font-weight: 600; color: var(--white); }
  .option-dark .website { left: 375px; top: 264px; font-size: 20px; font-weight: 600; color: var(--white); }

  /* Option 2 */
  .option-light { top: 423px; background: linear-gradient(180deg, #ffffff 0%, #ffffff 40%, var(--ice) 100%); border: 1px solid var(--mist); }
  .option-light .waves { left: 0; top: 205px; width: 746px; height: 149px;
    background: linear-gradient(170deg, rgba(255,255,255,0) 0%, var(--sky) 35%, var(--blue) 60%, var(--mist) 100%);
    border-radius: 50% 50% 0 0 / 30% 45% 0 0; opacity: 0.9; }
  .option-light .brand-name { left: 68px; top: 125px; width: 260px; }
  .option-light .brand-name .big { font-size: 47px; }
  .option-light .brand-name .small { font-size: 30px; margin-top: 6px; }
  .option-light .tagline { left: 367px; top: 78px; font-size: 33px; font-weight: 600; color: var(--navy); }
  .option-light .phone { left: 366px; top: 114px; font-size: 68px; font-weight: 600; color: var(--navy); letter-spacing: -1px; }
  .option-light .service-bar { left: 371px; top: 185px; width: 289px; height: 28px; display: flex; background: var(--orange); }
  .service-bar span { flex: auto; display: flex; align-items: center; justify-content: center;
    color: var(--white); font-size: 21px; font-weight: 600; border-left: 1px solid rgba(255,255,255,0.7); }
  .service-bar span:first-child { border-left: 0; }
  .option-light .website { right: 85px; top: 219px; font-size: 22px; font-weight: 700; color: var(--navy); }
  .option-light .website .accent { color: var(--orange); }

  /* Option 3 */
  .option-indigo { top: 794px; background: var(--indigo); }
  .option-indigo .halftone { left: 0; top: 0; width: 746px; height: 210px;
    background: linear-gradient(160deg, rgba(140,198,63,0.85) 0%, rgba(39,36,92,0) 28%, rgba(39,36,92,0) 45%, rgba(140,198,63,0.7) 70%, rgba(200,230,120,0.95) 100%);
    -webkit-mask-image: linear-gradient(180deg, #000 0%, #000 55%, transparent 100%);
            mask-image: linear-gradient(180deg, #000 0%, #000 55%, transparent 100%); }
  .option-indigo .brand-name { left: 44px; top: 140px; width: 178px; }
  .option-indigo .brand-name .big { font-size: 34px; }
  .option-indigo .brand-name .small { font-size: 22px; margin-top: 3px; }
  .option-indigo .headline-a { left: 234px; top: 72px; font-family: "Barlow", Arial, sans-serif; font-size: 38px; font-weight: 700; color: var(--orange); }
  .option-indigo .headline-b { left: 232px; top: 108px; font-family: "Barlow", Arial, sans-serif; font-size: 53px; font-weight: 800; color: var(--orange); letter-spacing: -0.5px; }
  .option-indigo .headline-b .light { color: var(--white); }
  .option-indigo .services { left: 412px; top: 167px; font-size: 27px; font-weight: 600; color: var(--white); }
  .option-indigo .phone { left: 411px; top: 204px; font-size: 68px; font-weight: 600; color: var(--white); letter-spacing: -1px; }
  .option-indigo .website { left: 413px; top: 276px; font-size: 20px; font-weight: 600; color: var(--white); }
</style>
</head>
<body>

<section class="option option-dark">
  <div class="backdrop" role="img" aria-label="Angled blue geometric light streaks"></div>
  <div class="brand-name"><span class="line big">BRIGHTWATER</span><span class="line small">DWELLING SERVICES</span></div>
  <div class="phone">302<span class="dot">.</span>517<span class="dot">.</span>9046</div>
  <div class="headline-a">INDOOR <span class="light">AIR</span></div>
  <div class="headline-b">RESTORATION</div>
  <div class="services">Find<span class="sep">|</span>Fix<span class="sep">|</span>Mold<span class="sep">|</span>Odor<span class="sep">|</span>Allergens</div>
  <div class="website">www.brightwaterdwell.com</div>
</section>
<div class="option-label" style="top:375px">OPTION 1</div>

<section class="option option-light">
  <div class="waves" role="img" aria-label="Flowing blue air waves"></div>
  <div class="brand-name"><span class="line big">BRIGHTWATER</span><span class="line small">DWELLING SERVICES</span></div>
  <div class="tagline">INDOOR AIR RESTORATION</div>
  <div class="phone">302<span class="dot">.</span>517<span class="dot">.</span>9046</div>
  <div class="service-bar"><span>FIND</span><span>FIX</span><span>MOLD</span><span>ODOR</span><span>ALLERGENS</span></div>
  <div class="website"><span class="accent">www.</span>bright<span class="accent">water</span>dwell.com</div>
</section>
<div class="option-label" style="top:748px">OPTION 2</div>

<section class="option option-indigo">
  <div class="halftone" role="img" aria-label="Green halftone dots and sweeping lime curves"></div>
  <div class="brand-name"><span class="line big">BRIGHTWATER</span><span class="line small">DWELLING SERVICES</span></div>
  <div class="headline-a">INDOOR</div>
  <div class="headline-b"><span class="light">AIR</span> RESTORATION</div>
  <div class="services">Find<span class="sep">|</span>Fix<span class="sep">|</span>Mold<span class="sep">|</span>Odor<span class="sep">|</span>Allergens</div>
  <div class="phone">302<span class="dot">.</span>517<span class="dot">.</span>9046</div>
  <div class="website">www.brightwaterdwell.com</div>
</section>
<div class="option-label" style="top:1122px">OPTION 3</div>

</body>
</html>
```